Redesign of business card for Cedar Ridge Mechanical

We are looking for a new design for our business cards for Cedar Ridge Mechanical. We are a plumbing & HVAC construction company, operating on the West Coast of Canada and USA. Logo attached.
Industry/Entity Type
Construction - Plumbing & HVAC
Contact Information for Business Card
Name, address, phone numbers, email, website address
Look and feel
Each slider illustrates characteristics of the customer's brand and the style your logo design should communicate.

```html
<!DOCTYPE html>
<html lang="en">
<head>
<meta charset="utf-8">
<title>Cedar Ridge Mechanical – Business Card</title>
<link href="https://fonts.googleapis.com/css2?family=Oswald:wght@500&family=Montserrat:wght@400;600&display=swap" rel="stylesheet">
<style>
  :root {
    --backdrop: #6e5a44;
    --card-light: #ffffff;
    --card-dark: #262626;
    --ink: #1e1e1e;
    --ink-soft: #2b2b2b;
    --paper: #ffffff;
  }
  * { margin: 0; padding: 0; box-sizing: border-box; }
  html, body { width: 900px; height: 1200px; overflow: hidden; }
  body {
    position: relative;
    background: var(--backdrop);
    font-family: "Montserrat", Arial, sans-serif;
    color: var(--ink);
  }
  .card {
    position: absolute;
    border-radius: 22px;
    box-shadow: 0 6px 14px rgba(0,0,0,.35);
    overflow: hidden;
  }
  .card--front { left: 80px; top: 131px; width: 742px; height: 440px; background: var(--card-light); }
  .card--back  { left: 78px; top: 640px; width: 744px; height: 438px; background: var(--card-dark); }

  .company-name {
    position: absolute; left: 25px; top: 54px;
    font-family: "Oswald", "Arial Narrow", sans-serif; font-weight: 500;
    font-size: 35px; letter-spacing: 1.5px; text-transform: uppercase; color: var(--ink);
  }
  .person { position: absolute; right: 35px; top: 48px; text-align: right; }
  .person__name { font-weight: 600; font-size: 25px; line-height: 1.1; }
  .person__title { font-size: 15.5px; margin-top: 4px; }

  .address { position: absolute; left: 35px; top: 234px; font-size: 16px; line-height: 20px; color: var(--ink-soft); }

  .contacts { position: absolute; left: 36px; top: 316px; list-style: none; }
  .contacts li { display: flex; align-items: center; gap: 12px; font-size: 15.5px; height: 30px; color: var(--ink-soft); }
  .contacts svg { width: 15px; height: 15px; fill: var(--ink); flex: none; }

  .wordmark {
    position: absolute; display: flex; align-items: center; gap: 12px;
    font-family: "Oswald", "Arial Narrow", sans-serif; font-weight: 500;
    text-transform: uppercase; letter-spacing: 1px; white-space: nowrap;
  }
  .wordmark__square { display: block; flex: none; }
  .card--front .wordmark { right: 38px; top: 318px; font-size: 22px; color: var(--ink); }
  .card--front .wordmark__square { width: 22px; height: 22px; background: var(--ink); }
  .card--back .wordmark {
    left: 50%; top: 50%; transform: translate(-50%, -50%);
    font-size: 38px; color: var(--paper);
  }
  .card--back .wordmark__square { width: 36px; height: 36px; background: var(--paper); }
</style>
</head>
<body>

<section class="card card--front" aria-label="Business card front">
  <h1 class="company-name">Cedar Ridge Mechanical</h1>

  <div class="person">
    <p class="person__name">Daniel Hayes</p>
    <p class="person__title">Managing Director</p>
  </div>

  <address class="address">48 Alder Creek Road<br>Bellingham, WA 98225</address>

  <ul class="contacts">
    <li>
      <svg viewBox="0 0 24 24" aria-hidden="true"><path d="M6.6 10.8a15.1 15.1 0 0 0 6.6 6.6l2.2-2.2c.3-.3.7-.4 1-.2 1.1.4 2.3.6 3.6.6.6 0 1 .4 1 1V20c0 .6-.4 1-1 1A17 17 0 0 1 3 4c0-.6.4-1 1-1h3.5c.6 0 1 .4 1 1 0 1.3.2 2.5.6 3.6.1.3 0 .7-.2 1z"/></svg>
      888.555.0142
    </li>
    <li>
      <svg viewBox="0 0 24 24" aria-hidden="true"><path d="M2 5h20v2l-10 6L2 7zM2 9l10 6 10-6v10H2z"/></svg>
      info@cedarridgemechanical.com
    </li>
    <li>
      <svg viewBox="0 0 24 24" aria-hidden="true"><path d="M12 2a10 10 0 1 0 0 20 10 10 0 0 0 0-20zm0 2c1 0 2.3 1.8 2.8 5H9.2C9.7 5.8 11 4 12 4zM4.3 9h3c-.1.6-.1 1.3-.1 2v1H4.1A8 8 0 0 1 4.3 9zm0 6h3c.3 2 .9 3.6 1.6 4.5A8 8 0 0 1 4.3 15zm4.9 0h5.6c-.5 3.2-1.8 5-2.8 5s-2.3-1.8-2.8-5zm6.8 4.5c.7-.9 1.3-2.5 1.6-4.5h3a8 8 0 0 1-4.6 4.5zM16.8 12v-1c0-.7 0-1.4-.1-2h3a8 8 0 0 1 .2 3z"/></svg>
      www.cedarridgemechanical.com
    </li>
  </ul>

  <div class="wordmark"><span class="wordmark__square"></span>Cedar Ridge Mechanical</div>
</section>

<section class="card card--back" aria-label="Business card back">
  <div class="wordmark"><span class="wordmark__square"></span>Cedar Ridge Mechanical</div>
</section>

</body>
</html>
```